IT Freelancer (Consulting, trainer and project manager) needed letterhead

As a freelancer for IT Trainingswhip, consulting and project management I need a letterhead design. What is desired is a design that fits the existing logo (see Annex). It is functional, reliable, and equal time wirkenn Agil and modern. The whole is in color, as well as printed out to make a good impression on a black and white printer. The whole is to the existing Cooperate design (business card, homepage, logo) fit. Therefore, the choice of colors.
Updates

Target Market(s)

Customers such as medium-sized enterprises, training institutions

Industry/Entity Type

Consulting

Colors
0455a3
3277b5
85abd2
cfdfed
34a6d7
32a6d6
249fd4
0792cd
85cae6

Requirements
Must have
• Must include logo (see Annex) address (Brunnerweg 14, 95617 Waldsassen, Germany). Must seriously and act simultaneously Agil. Design should (even) be adaptable (signature, address, etc.) design must look good on a black / white laser

```html
<!DOCTYPE html>
<html lang="en">
<head>
<meta charset="UTF-8">
<title>Lorenz Haller – Letterhead</title>
<link rel="stylesheet" href="https://fonts.googleapis.com/css2?family=Lato:wght@300;400;700&display=swap">
<style>
  :root {
    --brand-navy: #0455a3;
    --brand-blue: #3277b5;
    --brand-sky: #34a6d7;
    --brand-mist: #cfdfed;
    --watermark: #eef4fa;
    --ink: #2b2b2b;
    --ink-soft: #555a60;
    --paper: #ffffff;
    --backdrop: #e9eaec;
  }
  * { margin: 0; padding: 0; box-sizing: border-box; }
  html, body {
    width: 1200px;
    height: 1200px;
    overflow: hidden;
    background: var(--backdrop);
    font-family: "Lato", sans-serif;
  }
  .stage {
    width: 1200px;
    height: 1200px;
    display: flex;
    align-items: center;
    justify-content: center;
  }
  .letterhead {
    position: relative;
    width: 778px;
    height: 1100px;
    background: var(--paper);
    box-shadow: 0 2px 12px rgba(0,0,0,0.08);
    overflow: hidden;
  }
  .watermark {
    position: absolute;
    left: 230px;
    top: 250px;
    width: 400px;
    height: 400px;
    border-radius: 50%;
    background: var(--watermark);
  }
  .brand {
    position: absolute;
    left: 48px;
    top: 62px;
    display: flex;
    align-items: center;
    gap: 14px;
  }
  .brand-dot {
    width: 64px;
    height: 64px;
    border-radius: 50%;
    background: var(--brand-navy);
  }
  .brand-name {
    font-weight: 700;
    font-size: 24px;
    letter-spacing: 0.04em;
    text-transform: uppercase;
    color: var(--brand-navy);
    line-height: 1.05;
  }
  .letter-body {
    position: absolute;
    left: 150px;
    top: 240px;
    width: 560px;
    color: var(--ink);
    font-size: 13px;
    line-height: 1.75;
  }
  .salutation { margin-bottom: 14px; }
  .letter-body p + p { margin-top: 26px; }
  .closing {
    position: absolute;
    left: 260px;
    top: 650px;
  }
  .signature-mark {
    display: block;
    width: 110px;
    height: 46px;
    background: linear-gradient(90deg, #f3f3f3, #e6e6e6);
    margin-bottom: 10px;
  }
  .signer-name {
    font-size: 17px;
    color: var(--ink);
  }
  .signer-role {
    font-size: 13px;
    font-weight: 300;
    color: var(--ink-soft);
    margin-top: 4px;
  }
</style>
</head>
<body>
<main class="stage">
  <article class="letterhead">
    <div class="watermark"></div>

    <header class="brand">
      <span class="brand-dot"></span>
      <span class="brand-name">Lorenz<br>Haller</span>
    </header>

    <section class="letter-body">
      <p class="salutation">Dear Mr. Smith,</p>
      <p>Lorem ipsum dolor sit amet, consectetur adipiscing elit. Donec orci purus, luctus vitae dignissim eu, iaculis sed purus. Vivamus faucibus, ipsum nec aliquet viverra, leo mauris condimentum ligula, sit amet sagittis enim ligula quis arcu. Nam egestas tortor id nisi porttitor mattis. In tortor ante, ultricies in suscipit a, tempus non massa. Vivamus et auctor mi. Fusce vel massa nulla. Phasellus nec eros mauris, et scelerisque orci. Donec malesuada orci vitae nulla accumsan porta a id massa. Quisque accumsan iaculis magna sit amet fringilla. Maecenas consequat, magna eget tincidunt semper, odio nibh rutrum mi, id feugiat ante nisi eu risus. Vestibulum nunc orci, rhoncus a placerat in, ultricies in mi. Cras mattis varius eros, vel fringilla nisi suscipit eget.</p>
      <p>Quisque scelerisque sagittis nulla at porttitor. Mauris a justo et tellus interdum tristique. Sed id augue vitae urna euismod commodo aliquet a quam. Pellentesque arcu velit, cursus et malesuada ut, consequat et diam. Nullam erat sem, rhoncus id ullamcorper vitae, rhoncus et arcu. In ultricies ultricies nulla, ut rutrum nisi iaculis at. Donec eu magna a metus ornare faucibus. Fusce aliquet faucibus ultricies. Morbi semper, est id tincidunt gravida, sem arcu adipiscing lacus, ac bibendum nulla leo eu purus. Quisque nec diam sed risus consectetur accumsan quis quis nibh. Vestibulum id purus lorem.</p>
    </section>

    <footer class="closing">
      <span class="signature-mark" role="img" aria-label="Handwritten signature"></span>
      <p class="signer-name">John Doe</p>
      <p class="signer-role">Co-Founder &amp; CEO</p>
    </footer>
  </article>
</main>
</body>
</html>
```